Norrell Advisory WA Business Card

Create an interesting, eye catching and colourful two sided business card. We are a business consulting operation assisting SME's improve all areas of their business. We provide consulting services to assist SME's to create a culture of continuous improvement, making a positive difference in the business. Our tag line is Small changes, big rewards. We want to create a well recognised, innovative brand that can be continued throughout our website, social media and email correspondence.

Target Market(s)

Small to Medium Enterprise Business Owners

Industry/Entity Type

Business Consultant

Contact Information for Business Card

Name of Business: Norrell Advisory - Steady Steps Lasting Gains
Derek Holloway Ph 0407385510 Megan Holloway Ph 0407913847
Email norrelladvisorywa@mailbox-example.com
Web address TBA
FaceBook page TBA

BACKSIDE OF CARD

Providing assistance with:

• Organisation & Efficiency
• Revenue generation & Marketing
• Financial Management
• Production quality & delivery
• Systems & Process documentation
• Exit Strategy

Font styles to use
Other font styles liked:
• Calibri

Colors

Designer to choose colors to be used in the design.

Requirements
Must have
• Calibri font

```html
<!DOCTYPE html>
<html lang="en">
<head>
<meta charset="utf-8">
<title>Norrell Advisory WA – Business Card</title>
<link href="https://fonts.googleapis.com/css2?family=Open+Sans:ital,wght@0,400;0,600;0,700;1,700&display=swap" rel="stylesheet">
<style>
  :root {
    --page: #e4e4e4;
    --card-front: #ffffff;
    --card-back-top: #232323;
    --card-back-bottom: #161616;
    --blue: #0b7bc1;
    --orange: #fbb034;
    --red: #ee4535;
    --green: #6db33f;
    --ink: #3f3f3f;
    --ink-soft: #555555;
    --ink-muted: #8a8a8a;
    --rule: #9a9a9a;
    --back-text: #d8d8d8;
  }
  * { box-sizing: border-box; margin: 0; padding: 0; }
  html, body {
    width: 1125px; height: 1200px; overflow: hidden;
    background: var(--page);
    font-family: "Open Sans", Calibri, sans-serif;
  }
  .canvas { position: relative; width: 1125px; height: 1200px; }

  .card { position: absolute; left: 171px; width: 826px; height: 472px; }
  .card--front { top: 106px; background: var(--card-front); }
  .card--back {
    top: 639px;
    background: linear-gradient(160deg, var(--card-back-top), var(--card-back-bottom));
  }

  /* brand lockup */
  .brand {
    position: absolute; left: 48px; top: 120px; width: 340px;
    text-align: center;
  }
  .brand__mark {
    display: block; width: 92px; height: 92px; margin: 0 auto 34px;
    background: var(--blue);
  }
  .brand__name {
    font-weight: 700; font-size: 30px; letter-spacing: 0.5px;
    color: var(--ink); text-transform: uppercase; line-height: 1;
  }
  .brand__tagline {
    margin-top: 8px; font-size: 13px; letter-spacing: 3px;
    color: var(--ink-muted); text-transform: uppercase;
  }

  /* contacts */
  .contacts { position: absolute; left: 433px; top: 66px; }
  .person__name {
    font-weight: 700; font-size: 33px; line-height: 40px;
    text-transform: uppercase;
  }
  .person__phone { font-weight: 700; font-size: 26px; line-height: 32px; }
  .person + .person { margin-top: 6px; }
  .person--derek .person__name { color: var(--blue); }
  .person--derek .person__phone { color: var(--orange); }
  .person--megan .person__name { color: var(--red); }
  .person--megan .person__phone { color: var(--green); }

  .links { list-style: none; margin-top: 2px; }
  .links li {
    display: flex; align-items: center; gap: 10px;
    font-size: 17px; line-height: 25px; color: var(--ink-soft);
  }
  .links svg { width: 17px; height: 17px; flex: none; }

  /* services */
  .services { position: absolute; left: 53px; width: 713px; top: 334px; }
  .services__heading {
    display: flex; align-items: center; gap: 6px;
    font-weight: 700; font-style: italic; font-size: 26px; color: var(--ink-soft);
    line-height: 36px;
  }
  .services__heading::before, .services__heading::after {
    content: ""; flex: 1; height: 1px; background: var(--rule);
  }
  .services__list {
    list-style: none; text-align: center;
    font-size: 17.5px; line-height: 24px; color: var(--ink-muted);
    padding-bottom: 12px; border-bottom: 1px solid var(--rule);
  }
  .services__row { display: block; }
  .services__row span + span::before { content: "\2022"; color: var(--ink-soft); margin: 0 3px; }

  /* back */
  .back__name {
    position: absolute; left: 0; right: 0; top: 180px; text-align: center;
    font-weight: 700; font-size: 46px; letter-spacing: 1px;
    color: #ffffff; text-transform: uppercase;
  }
  .back__tagline {
    position: absolute; left: 0; right: 0; top: 394px; text-align: center;
    font-size: 26px; text-transform: uppercase; color: var(--back-text);
  }
</style>
</head>
<body>
<main class="canvas">

  <section class="card card--front" aria-label="Card front">
    <div class="brand">
      <span class="brand__mark" aria-hidden="true"></span>
      <div class="brand__name">Norrell Advisory</div>
      <div class="brand__tagline">Steady Steps Lasting Gains</div>
    </div>

    <div class="contacts">
      <div class="person person--derek">
        <div class="person__name">Derek Holloway</div>
        <div class="person__phone">0407385510</div>
      </div>
      <div class="person person--megan">
        <div class="person__name">Megan Holloway</div>
        <div class="person__phone">0407913847</div>
      </div>
      <ul class="links">
        <li>
          <svg viewBox="0 0 16 16" aria-hidden="true"><rect x="1" y="1" width="14" height="14" fill="#1f5f9e"/></svg>
          norrelladvisorywa
        </li>
        <li>
          <svg viewBox="0 0 16 16" aria-hidden="true"><rect x="1" y="3" width="14" height="10" fill="#1f5f9e"/><path d="M1.5 3.5 8 9l6.5-5.5" fill="none" stroke="#fff" stroke-width="1.3"/></svg>
          norrelladvisorywa@mailbox-example.com
        </li>
        <li>
          <svg viewBox="0 0 16 16" aria-hidden="true"><circle cx="8" cy="8" r="7" fill="#1f5f9e"/><ellipse cx="8" cy="8" rx="3" ry="7" fill="none" stroke="#fff" stroke-width="1"/><path d="M1 8h14" stroke="#fff" stroke-width="1"/></svg>
          www.norrelladvisorywa.example
        </li>
      </ul>
    </div>

    <div class="services">
      <h2 class="services__heading">Providing assistance with</h2>
      <ul class="services__list">
        <li class="services__row"><span>Organisation &amp; Efficiency</span><span>Revenue generation &amp; Marketing</span><span>Financial Management</span></li>
        <li class="services__row"><span>Production quality &amp; delivery</span><span>Systems &amp; Process documentation</span><span>Exit Strategy</span></li>
      </ul>
    </div>
  </section>

  <section class="card card--back" aria-label="Card back">
    <div class="back__name">Norrell Advisory</div>
    <div class="back__tagline">Steady Steps Lasting Gains</div>
  </section>

</main>
</body>
</html>
```